4D Cradle Glimpse Luxury Ultrasound Billboard

Design a HIGH-END, MODERN billboard for my private prenatal ultrasound studio, 4D Cradle Glimpse, located in Pace, Florida.
This billboard will be viewed by drivers traveling at highway speeds, so it must be extremely clean, simple, and readable within 6 seconds.
About My Business
4D Cradle Glimpse is a private prenatal ultrasound studio specializing in:
Highest technology 4D/HD Ultrasounds
Early Gender Determination
Pregnancy Confirmation
I have been serving families for nearly 10 years and is known for creating a memorable experience, not just an ultrasound appointment.
Design Style
I DO NOT want:
Flowers
Leaves
Swirls
Glitter
Hearts everywhere
Busy backgrounds
Generic maternity stock graphics
I DO want:
Modern
Luxury
Upscale
Clean
Professional
Eye-catching
Premium medical spa feel
Colors
Use colors from my logo:
LOGO Green ( or a deep green)
Black
White
Soft Gold accents
Images:
Incorporate my professional headshot in a clean, modern way, logo, and the ultrasound images
Text
Keep wording minimal.
Primary Headline ( OPEN TO IDEAS) :
EXAMPLES ( WOULD RATHER SOMETHING MORE CATCHY)
" ADVANCED IMAGING. UNFORGETTABLE MOMENTS"
"MEET YOUR BABY BEFORE BIRTH"
Under headline:
4D Ultrasound • Early Gender • Pregnancy Confirmation
Business Name:
4D Cradle Glimpse
Private Prenatal Ultrasound Studio
Phone Number:
850-471-5923
Important
This billboard must be readable in 5–6 seconds from a moving vehicle.
Less text is better.
The phone number and business name must be visible from a distance.
The design should feel like a premium brand that immediately tells expecting parents:
“This is where I go to see my baby.”
Files Provided
Official logo
Headshot
Ultrasound images
Don’t make this look like a medical office billboard.
Make it look like a luxury baby experience billboard. That’s what separates 4D Cradle Glimpse from hospitals, OB offices, and all the new studios popping up around you. The emotional connection is what gets moms to book. ❤️
Billboard Size - 10.6” x 36”

```html
<!DOCTYPE html>
<html lang="en">
<head>
<meta charset="utf-8">
<title>4D Cradle Glimpse Billboard</title>
<link href="https://fonts.googleapis.com/css2?family=Libre+Baskerville:wght@400;700&family=Montserrat:wght@700;800&display=swap" rel="stylesheet">
<style>
  :root {
    --page-bg: #cfcfcf;
    --white: #ffffff;
    --sage: #5e6e68;
    --gold: #c69a35;
    --scrub: #3f5a3c;
    --hair: #e6d2b0;
  }
  * { margin: 0; padding: 0; box-sizing: border-box; }
  html, body { width: 1200px; height: 1160px; overflow: hidden; background: var(--page-bg); }
  .billboard {
    position: absolute; left: 40px; top: 415px;
    width: 1120px; height: 330px;
    background: var(--white); overflow: hidden;
  }
  .band-left {
    position: absolute; left: 0; top: 237px; width: 520px; height: 93px;
    background: var(--sage);
  }
  .band-right {
    position: absolute; left: 520px; top: 256px; width: 600px; height: 74px;
    background: var(--sage);
  }
  .band-rule {
    position: absolute; left: 720px; top: 253px; width: 400px; height: 2px;
    background: var(--sage);
  }
  .brand-box {
    position: absolute; left: 35px; top: 26px; width: 461px; height: 224px;
    background: var(--white); border: 4px solid var(--sage); border-radius: 26px;
    display: flex; align-items: center; justify-content: center; text-align: center;
  }
  .brand-name {
    font-family: "Libre Baskerville", Georgia, serif; font-weight: 700;
    font-size: 52px; line-height: 1.15; color: var(--sage);
  }
  .phone {
    position: absolute; left: 32px; top: 252px;
    display: flex; align-items: center; gap: 8px;
    font-family: "Montserrat", Arial, sans-serif; font-weight: 800;
    font-size: 50px; color: var(--white); letter-spacing: 0.5px;
  }
  .phone svg { width: 38px; height: 38px; }
  .portrait {
    position: absolute; left: 515px; top: 26px; width: 221px; height: 304px;
    background: linear-gradient(180deg, var(--hair) 0%, #d9bf9a 35%, var(--scrub) 60%, #2f4a2d 100%);
  }
  .scan-frame {
    position: absolute; left: 682px; top: 218px; width: 102px; height: 102px;
    border-radius: 50%; border: 3px solid var(--sage);
    background: radial-gradient(circle, #b5786a 0%, #7a3f36 70%, #3a1d18 100%);
  }
  .headline {
    position: absolute; left: 752px; top: 18px; width: 340px;
    font-family: "Libre Baskerville", Georgia, serif; font-weight: 700;
    text-align: center; line-height: 1;
  }
  .headline .lead { display: block; font-size: 37px; color: var(--sage); }
  .headline .accent { display: block; font-size: 72px; color: var(--gold); margin-top: 10px; }
  .headline .anchor { display: block; font-size: 80px; color: var(--sage); margin-top: 2px; }
  .services {
    position: absolute; left: 800px; top: 262px; list-style: none;
    font-family: "Libre Baskerville", Georgia, serif; font-size: 18px;
    color: var(--white); line-height: 1.35;
  }
</style>
</head>
<body>
  <div class="billboard">
    <div class="band-left"></div>
    <div class="band-right"></div>
    <div class="band-rule"></div>

    <div class="brand-box">
      <div class="brand-name">4D Cradle<br>Glimpse</div>
    </div>

    <div class="phone">
      <svg viewBox="0 0 24 24" aria-hidden="true">
        <path fill="#fff" d="M6.6 10.8a15.1 15.1 0 0 0 6.6 6.6l2.2-2.2a1 1 0 0 1 1-.25 11.4 11.4 0 0 0 3.6.57 1 1 0 0 1 1 1V20a1 1 0 0 1-1 1A17 17 0 0 1 3 4a1 1 0 0 1 1-1h3.5a1 1 0 0 1 1 1c0 1.25.2 2.45.57 3.57a1 1 0 0 1-.25 1z"/>
        <path fill="none" stroke="#fff" stroke-width="1.8" stroke-linecap="round" d="M14 3.5a7 7 0 0 1 6.5 6.5M14 7a3.5 3.5 0 0 1 3 3"/>
      </svg>
      <span>850-471-5923</span>
    </div>

    <div class="portrait" role="img" aria-label="Headshot of the studio owner in green scrubs holding an ultrasound probe"></div>
    <div class="scan-frame" role="img" aria-label="4D ultrasound image of twin babies"></div>

    <h1 class="headline">
      <span class="lead">Meet Your Baby</span>
      <span class="accent">BEFORE</span>
      <span class="anchor">BIRTH</span>
    </h1>

    <ul class="services">
      <li>• 4D Ultrasound • Early Gender</li>
      <li>• Pregnancy Confirmation</li>
    </ul>
  </div>
</body>
</html>
```